Norrell Advisory WA Business Card

Create an interesting, eye catching and colourful two sided business card. We are a business consulting operation assisting SME's improve all areas of their business. We provide consulting services to assist SME's to create a culture of continuous improvement, making a positive difference in the business. Our tag line is Small changes, big rewards. We want to create a well recognised, innovative brand that can be continued throughout our website, social media and email correspondence.

Target Market(s)

Small to Medium Enterprise Business Owners

Industry/Entity Type

Business Consultant

Contact Information for Business Card

Name of Business: Norrell Advisory - Steady Steps Strong Results
Derek Holloway Ph 0407385510 Megan Holloway Ph 0407913847
Email norrelladvisorywa@mailbox-example.com
Web address TBA
FaceBook page TBA

BACKSIDE OF CARD

Providing assistance with:

• Organisation & Efficiency
• Revenue generation & Marketing
• Financial Management
• Production quality & delivery
• Systems & Process documentation
• Exit Strategy

Font styles to use
Other font styles liked:
• Calibri

Colors

Designer to choose colors to be used in the design.

Requirements
Must have
• Calibri font

```html
<!DOCTYPE html>
<html lang="en">
<head>
<meta charset="utf-8">
<title>Norrell Advisory WA – Business Card</title>
<link rel="stylesheet" href="https://fonts.googleapis.com/css2?family=Carlito:wght@400;700&family=Oswald:wght@400&display=swap">
<style>
  :root {
    --stage: #2b2b2d;
    --card: #1a1a1b;
    --white: #f2f2f2;
    --grey: #9a9a9a;
    --name-grey: #c4c4c4;
    --blue: #1e8fd6;
    --yellow: #f5b824;
    --red: #e8412f;
    --green: #7cbf3a;
  }
  * { box-sizing: border-box; margin: 0; padding: 0; }
  html, body { width: 1200px; height: 900px; overflow: hidden; }
  body {
    background: var(--stage);
    font-family: "Carlito", "Calibri", sans-serif;
    color: var(--white);
    position: relative;
  }
  .card {
    position: absolute;
    left: 300px;
    width: 600px;
    height: 350px;
    background: var(--card);
    border-radius: 22px;
    overflow: hidden;
    box-shadow: 0 10px 30px rgba(0,0,0,.45);
  }
  .card--back { top: 75px; }
  .card--front { top: 475px; }

  /* back side */
  .services {
    position: absolute;
    top: 70px; left: 0; right: 0;
    text-align: center;
    text-transform: uppercase;
    letter-spacing: .5px;
  }
  .services__title { font-size: 22px; font-weight: 700; margin-bottom: 22px; }
  .services__list { list-style: none; font-size: 17px; line-height: 27px; }
  .brand-dot--edge {
    position: absolute;
    right: -40px; top: 40px;
    width: 90px; height: 90px;
    border-radius: 50%;
    background: var(--blue);
  }

  /* front side */
  .brand {
    position: absolute;
    top: 62px; left: 150px;
    display: flex; align-items: center; gap: 16px;
  }
  .brand-dot { width: 62px; height: 62px; border-radius: 50%; background: var(--blue); flex: none; }
  .brand__name { font-size: 32px; font-weight: 700; letter-spacing: 1px; text-transform: uppercase; line-height: 1; }
  .brand__tagline {
    font-family: "Oswald", "Arial Narrow", sans-serif;
    font-size: 16px; color: var(--grey);
    text-transform: uppercase; letter-spacing: .5px; margin-top: 6px;
  }
  .rule {
    position: absolute;
    top: 205px; left: 272px; width: 304px; height: 3px;
    display: flex;
  }
  .rule span { flex: 1; }
  .rule .y { background: var(--yellow); }
  .rule .b { background: var(--blue); }
  .rule .r { background: var(--red); }
  .rule .g { background: var(--green); }

  .people { position: absolute; left: 30px; top: 190px; }
  .person { margin-bottom: 12px; }
  .person__name { font-size: 27px; font-weight: 700; color: var(--name-grey); text-transform: uppercase; line-height: 1; }
  .person__phone { font-size: 17px; color: var(--blue); margin-top: 3px; }

  .contacts { position: absolute; left: 300px; top: 222px; list-style: none; font-size: 15px; line-height: 24px; }
  .contacts li { display: flex; align-items: center; gap: 7px; }
  .contacts svg { width: 14px; height: 14px; flex: none; }
</style>
</head>
<body>

<section class="card card--back" aria-label="Card back">
  <div class="services">
    <h2 class="services__title">Providing assistance with:</h2>
    <ul class="services__list">
      <li>Organisation &amp; Efficiency</li>
      <li>Revenue Generation &amp; Marketing</li>
      <li>Financial Management</li>
      <li>Production Quality &amp; Delivery</li>
      <li>Systems &amp; Process Documentation</li>
      <li>Exit Strategy</li>
    </ul>
  </div>
  <div class="brand-dot--edge" aria-hidden="true"></div>
</section>

<section class="card card--front" aria-label="Card front">
  <div class="brand">
    <div class="brand-dot" aria-hidden="true"></div>
    <div>
      <div class="brand__name">Norrell Advisory</div>
      <div class="brand__tagline">Steady Steps Strong Results</div>
    </div>
  </div>

  <div class="rule" aria-hidden="true"><span class="y"></span><span class="b"></span><span class="r"></span><span class="g"></span></div>

  <div class="people">
    <div class="person">
      <div class="person__name">Derek Holloway</div>
      <div class="person__phone">0407385510</div>
    </div>
    <div class="person">
      <div class="person__name">Megan Holloway</div>
      <div class="person__phone">0407913847</div>
    </div>
  </div>

  <ul class="contacts">
    <li>
      <svg viewBox="0 0 14 14" aria-hidden="true"><rect x="1" y="3" width="12" height="8" fill="#1e8fd6"/><path d="M1 3 L7 8 L13 3" fill="none" stroke="#1a1a1b" stroke-width="1.2"/></svg>
      norrelladvisorywa@mailbox-example.com
    </li>
    <li>
      <svg viewBox="0 0 14 14" aria-hidden="true"><circle cx="7" cy="7" r="6" fill="#1e8fd6"/><path d="M1 7 H13 M7 1 C4 4 4 10 7 13 M7 1 C10 4 10 10 7 13" fill="none" stroke="#1a1a1b" stroke-width="1"/></svg>
      www.norrelladvisory.example
    </li>
    <li>
      <svg viewBox="0 0 14 14" aria-hidden="true"><circle cx="7" cy="7" r="6" fill="#1e8fd6"/></svg>
      social.norrelladvisory.example
    </li>
  </ul>
</section>

</body>
</html>
```